Redo our website for our Robotics company

We sell robotic equipment to the restaurant industry. Our current robot, is a cooking robot that cooks up to 15 lbs of food. We will provide a prior website as well as brand guidelines. We plan on using wordpress and take advantage of wordpress's visual (no code) editor.

Current website - https://kelvatrix88.com/ (please note we are only selling Tammo now and no longer selling Plavo+

We want someone to take our existing content and design the website as well as layout our content we provide. Here's a suggested site layout:

✅ KelvaTrix88 Website Wireframe / Site Map
1. Home

Purpose: Introduce Tammo, establish credibility, drive demo requests.

Sections:

Hero Section

Headline: “Meet Tammo — Your New Robotic Chef for High-Volume, Consistent Cooking.”

Sub-headline: Increase throughput. Reduce labor. Deliver perfect food every time.

CTA: Request a Demo + Watch Tammo Cook

Visual: Video loop or hero animation of Tammo in action.

How Tammo Works (3-4 steps)

Step cards: Load Ingredients → Select Recipe → Tammo Cooks → Serve

Icons and short explanations.

Key Benefits

Labor savings

Zero inconsistency

24/7 uptime

Throughput increases (30–50% faster)

Health & safety compliance

Who It’s For

QSR restaurants

Fast casual

Catering/commissaries

Ghost kitchens

Case Studies / Testimonials

Logo bar + quotes

“Tammo helped us reduce cooking times by 40%.”

Video Section

“Watch Tammo cook a full batch from start to finish.”

CTA Section

Big banner: Book a Demo

2. Product: “Meet Tammo”

Purpose: Deep dive into hardware, software, safety, reliability.

Sections:

Overview

What Tammo is

What tasks it automates

Where it fits in a kitchen

Hardware Features

High-temperature cooking chamber

Precision sensors

Automated stirring

Automated dispensing

Safety mechanisms (locking lids, auto-shutoff)

Software & AI

Recipe automation

IoT dashboard

Remote monitoring

Predictive maintenance

Specs Table

Dimensions

Power requirements

Capacity (lbs per batch)

Safety certifications

Gallery

Close-ups, installation photos, process shots

CTA: Request a Demo

3. Solutions

Purpose: Show that Tammo solves real operational problems.

Sub-pages or sections:

For Quick-Service Restaurants

Reduce labor cost

Speed up peak-hour demand

For Catering & Commissaries

Large-batch consistency

Automate repetitive cooking tasks

For High-Growth Chains

Replicable quality across multiple locations

Centralized recipe control

Each solution page includes:

A problem statement

How Tammo solves it

Metrics / KPIs

Relevant testimonial

CTA

4. ROI / Economics

Purpose: Sell the financial story clearly.

Sections:

Savings Calculator

Labor hours saved

Cost savings

Throughput increases

Food waste reduction

Before & After Comparison

Traditional kitchen vs. robotic kitchen

Sample ROI

“Payback in as little as 3–6 months.”

Download Full ROI Report (PDF)

5. Case Studies

Purpose: Social proof + real results.

Structure for each case study:

Customer background

Problem

Implementation

KPIs achieved

Labor savings

Consistency improvements

Cooking speed

Quote + photos/video

6. Pricing

Purpose: Start a commercial conversation.

Include:

Subscription model (monthly / annual)

Hardware leasing or purchase options

Installation + training

Support level

CTA to book a sales call

7. About

Purpose: Build trust.

Sections:

Mission statement

Founding team

Advisors/partners

“Why we built Tammo”

8. Resources

Purpose: SEO + education.

Subpages:

Blog (e.g., “The Future of Automated Kitchens”)

Whitepapers

Technical documentation

Product videos

9. Contact

General inquiry form

Sales contact

Support portal

Careers

```html
<!DOCTYPE html>
<html lang="en">
<head>
<meta charset="utf-8">
<title>KelvaTrix88 — Meet Tammo</title>
<link href="https://fonts.googleapis.com/css2?family=Montserrat:ital,wght@0,400;0,500;0,600;0,700;0,800;1,500&family=Oswald:wght@400&display=swap" rel="stylesheet">
<style>
:root{
  --navy:#0c2350;
  --red:#e32520;
  --orange:#f47b3b;
  --card:#2f5b95;
  --ice:#dde9f8;
  --brown:#2a1b12;
  --ink:#222;
}
*{box-sizing:border-box;margin:0;padding:0}
html,body{width:1200px;height:4161px;overflow:hidden}
body{font-family:"Montserrat",sans-serif;color:var(--ink);background:#fff;position:relative}
.abs{position:absolute}
.condensed{font-family:"Oswald",sans-serif;font-weight:400}

/* nav */
.site-nav{position:absolute;top:0;left:0;width:1200px;height:84px;background:#fff}
.brand{position:absolute;left:75px;top:24px;font-weight:800;font-size:30px;color:var(--red);letter-spacing:-.5px}
.nav-links{position:absolute;left:298px;top:34px;display:flex;gap:27px;font-size:14px;font-weight:500;color:#333;list-style:none}
.nav-links .active{color:var(--red);font-weight:700}

/* hero */
.hero{position:absolute;top:84px;left:0;width:1200px;height:638px;background:linear-gradient(90deg,#1c120c,var(--brown) 60%,#332116);overflow:hidden}
.hero-photo{position:absolute;left:0;top:0;width:640px;height:638px;
  background:radial-gradient(ellipse 45% 55% at 28% 45%,rgba(235,228,218,.55),transparent 70%),
             radial-gradient(ellipse 30% 40% at 72% 60%,rgba(90,90,92,.6),transparent 75%),
             linear-gradient(120deg,#4a3426,#1e1510 75%);
  clip-path:path("M0 0 H640 V638 H150 Q90 638 80 560 L0 60 Z")}
.hero-copy{position:absolute;right:75px;top:160px;text-align:right;color:#fff}
.hero-copy h1{font-size:40px;font-weight:700;line-height:45px;letter-spacing:.5px}
.hero-copy h1 span{color:var(--orange)}
.hero-copy p{font-size:33px;line-height:39px;margin-top:10px}
.btn{display:inline-flex;align-items:center;justify-content:center;height:62px;font-weight:700;font-size:20px;color:#fff;clip-path:polygon(8% 0,100% 0,92% 100%,0 100%)}
.btn-red{background:linear-gradient(90deg,var(--red),var(--orange))}
.hero-actions{position:absolute;right:75px;top:406px;display:flex;gap:8px}
.btn-outline{position:relative;width:306px;height:62px;display:flex;align-items:center;justify-content:center;color:#fff;font-weight:700;font-size:19px;gap:12px}
.btn-outline svg.frame{position:absolute;inset:0}

.sec-title{position:absolute;width:1200px;text-align:center;font-size:40px;font-weight:700;color:var(--navy)}

/* steps */
.step{position:absolute;top:898px;width:243px;height:184px;background:var(--card);border-radius:6px;color:#fff;text-align:center;overflow:hidden}
.step h3{margin-top:64px;font-size:19px;font-weight:700}
.step p{font-size:12.5px;line-height:20px;margin:6px 28px 0;color:#d9e3f1}
.step .num{position:absolute;right:12px;bottom:-18px;font-size:96px;font-style:italic;font-weight:800;color:rgba(255,255,255,.1)}
.step-icon{position:absolute;top:858px;width:80px;height:80px;border-radius:50%;background:var(--red);border:5px solid #fff;display:flex;align-items:center;justify-content:center}

/* benefits */
.benefits-band{position:absolute;top:1163px;left:0;width:1200px;height:638px;background:var(--ice);clip-path:path("M40 0 H1200 V638 H150 Q100 638 90 580 L0 60 Q0 0 40 0 Z")}
.machine{position:absolute;left:80px;top:1245px;width:420px;height:480px;
  background:radial-gradient(ellipse 38% 46% at 50% 48%,rgba(60,60,62,.85),rgba(120,120,124,.5) 55%,transparent 78%)}
.benefit{position:absolute;display:flex;gap:16px}
.benefit .ico{width:62px;height:62px;border-radius:50%;border:2px solid var(--navy);display:flex;align-items:center;justify-content:center;flex:none;background:var(--ice)}
.benefit .ico.on{background:var(--red);border-color:var(--red)}
.benefit h4{font-size:20px;font-weight:700;color:var(--red);margin-top:-4px}
.benefit p{font-size:12.5px;line-height:20px;color:#333;width:370px;margin-top:4px}

/* audience */
.aud{position:absolute;top:1946px;width:243px;height:302px;border-radius:6px;overflow:hidden;color:#fff}
.aud .ph{position:absolute;inset:0}
.aud .shade{position:absolute;inset:0;background:linear-gradient(180deg,transparent 45%,rgba(0,0,0,.9))}
.aud.hot .shade{background:linear-gradient(180deg,transparent 40%,rgba(227,37,32,.95))}
.aud h3{position:absolute;left:14px;top:218px;font-size:19px;font-weight:700}
.aud p{position:absolute;left:14px;top:246px;font-size:12.5px;line-height:20px;width:215px}

/* case studies */
.cases{position:absolute;top:2334px;left:0;width:1200px;height:403px;
  background:radial-gradient(ellipse 30% 45% at 80% 45%,rgba(240,60,60,.55),transparent 75%),
             linear-gradient(90deg,#1c2850 0%,#4b2a48 45%,#b8222a 75%,#d42828);color:#fff;text-align:center}
.cases h2{margin-top:58px;font-size:40px;font-weight:700}
.cases blockquote{margin:20px auto 0;width:560px;font-size:31px;font-style:italic;font-weight:500;line-height:42px}
.client{position:absolute;left:491px;top:240px;display:flex;gap:14px;align-items:center;text-align:left}
.client .mark{width:50px;height:50px;border-radius:50%;background:#f4b21a}
.client b{font-size:20px;font-weight:600;display:block}
.client span{font-size:16px}
.dots{position:absolute;left:564px;top:330px;display:flex;gap:11px}
.dots i{width:10px;height:10px;border-radius:50%;background:#fff}
.dots i:first-child{background:var(--red)}

/* video */
.video{position:absolute;left:136px;top:2925px;width:928px;height:412px;
  background:radial-gradient(ellipse 25% 40% at 78% 45%,rgba(170,172,176,.6),transparent 75%),
             radial-gradient(ellipse 30% 45% at 50% 55%,rgba(70,70,74,.8),transparent 75%),
             linear-gradient(90deg,#2b3147,#3d404a 50%,#5c5f66 75%,#2a2a2a)}
.play{position:absolute;left:430px;top:174px;width:66px;height:66px;border-radius:50%;border:3px solid #fff;background:rgba(0,0,0,.35);display:flex;align-items:center;justify-content:center}

/* cta */
.cta{position:absolute;top:3416px;left:0;width:1200px;height:420px;background:linear-gradient(90deg,#08183a,#112a5a 60%,#0a1c40);color:#fff;overflow:hidden}
.cta-photo{position:absolute;left:660px;top:0;width:480px;height:420px;
  background:radial-gradient(ellipse 30% 50% at 40% 55%,rgba(232,228,222,.5),transparent 75%),
             radial-gradient(ellipse 28% 38% at 72% 65%,rgba(110,110,116,.55),transparent 78%)}
.cta h2{position:absolute;left:75px;top:72px;font-weight:800;line-height:48px}
.cta h2 .l1{font-size:50px;display:block}
.cta h2 .l2{font-size:42px;display:block}
.cta p{position:absolute;left:75px;top:185px;font-size:33px;line-height:39px}
.cta .btn{position:absolute;left:75px;top:276px;width:260px}

/* footer */
.footer{position:absolute;top:3836px;left:0;width:1200px;height:325px;background:#fff}
.footer .brand{left:75px;top:72px;font-size:36px}
.footer .legal{position:absolute;left:75px;top:140px;font-size:12.5px;line-height:21px;color:#333}
.socials{position:absolute;left:75px;top:226px;display:flex;gap:18px}
.socials span{width:20px;height:20px;border-radius:50%;background:#222}
.fcol{position:absolute;top:70px}
.fcol h5{font-size:20px;font-weight:600;color:var(--navy);margin-bottom:14px}
.fcol ul{list-style:none;font-size:14px;line-height:34px;color:#222}
.fcol p{font-size:14px;line-height:26px}
.email{width:243px;height:52px;border:1px solid #ccc;border-radius:8px;font-size:14px;color:#444;padding:17px 16px}
.signup{margin-top:14px;width:108px;height:50px;border-radius:8px;background:var(--red);color:#fff;font-weight:700;font-size:16px;display:flex;align-items:center;justify-content:center}
</style>
</head>
<body>

<header class="site-nav">
  <div class="brand">KelvaTrix88</div>
  <ul class="nav-links">
    <li class="active">Home</li><li>Meet Tammo</li><li>Solutions</li><li>ROI / Economics</li><li>Case Studies</li><li>Pricing</li><li>About</li><li>Resources</li><li>Contact</li>
  </ul>
</header>

<section class="hero">
  <div class="hero-photo" role="img" aria-label="Chef in white uniform standing beside the Tammo cooking robot in a dark kitchen"></div>
  <div class="hero-copy">
    <h1><span>Meet Tammo</span>-Your New<br>Robotic Chef for High-Volume,<br>Consistent Cooking.</h1>
    <p class="condensed">Increase throughput. Reduce labor. Deliver<br>perfect food every time.</p>
  </div>
  <div class="hero-actions">
    <span class="btn btn-red" style="width:256px">Request a Demo</span>
    <span class="btn-outline">
      <svg class="frame" width="306" height="62"><polygon points="24,1 305,1 282,61 1,61" fill="none" stroke="#fff" stroke-width="2"/></svg>
      <svg width="20" height="20" viewBox="0 0 20 20"><circle cx="10" cy="10" r="8.5" fill="none" stroke="#fff" stroke-width="2"/><polygon points="8,6 14,10 8,14" fill="#fff"/></svg>
      Watch Tammo Cook
    </span>
  </div>
</section>

<h2 class="sec-title" style="top:782px">How Tammo Works</h2>
<div class="step" style="left:75px"><h3>Load Ingredients</h3><p>Sed ut perspiciatis unde omnis iste natus error sit vo luptatem accus.</p><span class="num">1</span></div>
<div class="step" style="left:345px"><h3>Select Recipe</h3><p>Sed ut perspiciatis unde omnis iste natus error sit vo luptatem accus.</p><span class="num">2</span></div>
<div class="step" style="left:615px"><h3>Tammo Cooks</h3><p>Sed ut perspiciatis unde omnis iste natus error sit vo luptatem accus.</p><span class="num">3</span></div>
<div class="step" style="left:884px"><h3>Serve</h3><p>Sed ut perspiciatis unde omnis iste natus error sit vo luptatem accus.</p><span class="num">4</span></div>
<div class="step-icon" style="left:156px"><svg width="26" height="26" viewBox="0 0 24 24" fill="#fff"><path d="M12 3l6 7h-4v6h-4v-6H6z"/><rect x="4" y="18" width="16" height="3"/></svg></div>
<div class="step-icon" style="left:426px"><svg width="26" height="26" viewBox="0 0 24 24" fill="#fff"><rect x="3" y="5" width="3" height="3"/><rect x="8" y="5" width="13" height="3"/><rect x="3" y="11" width="3" height="3"/><rect x="8" y="11" width="13" height="3"/><rect x="3" y="17" width="3" height="3"/><rect x="8" y="17" width="13" height="3"/></svg></div>
<div class="step-icon" style="left:696px"><svg width="26" height="26" viewBox="0 0 24 24" fill="none" stroke="#fff" stroke-width="3"><path d="M19 9a7 7 0 0 0-13-1M5 15a7 7 0 0 0 13 1"/><path d="M20 3v6h-6M4 21v-6h6"/></svg></div>
<div class="step-icon" style="left:965px"><svg width="26" height="26" viewBox="0 0 24 24" fill="#fff"><path d="M20 3c-6 0-10 4-12 9l4 4c5-2 9-6 9-12zM6 14l-3 2 2 1 2 2 1 2 2-3z"/></svg></div>

<div class="benefits-band"></div>
<div class="machine" role="img" aria-label="Tammo cooking robot unit in black and brushed steel on casters"></div>
<h2 class="abs" style="left:520px;top:1230px;font-size:40px;font-weight:700;color:var(--navy)">Key Benefits</h2>
<div class="benefit" style="left:495px;top:1303px"><div class="ico"><svg width="26" height="26" viewBox="0 0 24 24" fill="var(--navy)"><circle cx="12" cy="8" r="5"/><path d="M3 22c0-6 4-8 9-8s9 2 9 8z"/></svg></div><div><h4>Labor savings</h4><p>Sed ut perspiciatis unde omnis iste natus error sit vo luptatem accus.</p></div></div>
<div class="benefit" style="left:547px;top:1392px"><div class="ico"><svg width="26" height="26" viewBox="0 0 24 24" fill="var(--navy)"><rect x="3" y="10" width="4" height="11"/><path d="M9 10l4-7c2 0 2 2 2 3l-1 4h6c1 0 2 1 1 3l-2 7c0 1-1 1-2 1H9z"/></svg></div><div><h4>Zero inconsistency</h4><p>Sed ut perspiciatis unde omnis iste natus error sit vo luptatem accus.</p></div></div>
<div class="benefit" style="left:601px;top:1481px"><div class="ico on"><svg width="26" height="26" viewBox="0 0 24 24"><circle cx="12" cy="12" r="9" fill="#fff"/><path d="M12 7v5l3 2" stroke="var(--red)" stroke-width="2.5" fill="none"/></svg></div><div><h4>24/7 uptime</h4><p>Sed ut perspiciatis unde omnis iste natus error sit vo luptatem accus.</p></div></div>
<div class="benefit" style="left:547px;top:1571px"><div class="ico"><svg width="26" height="26" viewBox="0 0 24 24" fill="none" stroke="var(--navy)" stroke-width="2.5"><path d="M3 3v18h18"/><path d="M6 16l5-5 3 3 6-6"/></svg></div><div><h4>Throughput increases (30-50% faster)</h4><p>Sed ut perspiciatis unde omnis iste natus error sit vo luptatem accus.</p></div></div>
<div class="benefit" style="left:495px;top:1663px"><div class="ico"><svg width="28" height="26" viewBox="0 0 24 22"><path d="M12 21C4 15 1 11 1 7a5 5 0 0 1 11-2 5 5 0 0 1 11 2c0 4-3 8-11 14z" fill="var(--navy)"/><path d="M4 10h5l2-3 2 6 2-3h5" stroke="#fff" stroke-width="1.8" fill="none"/></svg></div><div><h4>Health &amp; safety compliance</h4><p>Sed ut perspiciatis unde omnis iste natus error sit vo luptatem accus.</p></div></div>

<h2 class="sec-title" style="top:1858px">Who It’s For</h2>
<div class="aud" style="left:75px"><div class="ph" role="img" aria-label="Warm-lit quick-service restaurant dining room" style="background:linear-gradient(170deg,#c98a4e,#8a4f2c 45%,#4a2a18)"></div><div class="shade"></div><h3>QSR restaurants</h3><p>Sed ut perspiciatis unde omnis iste natus error sit.</p></div>
<div class="aud" style="left:345px"><div class="ph" role="img" aria-label="Two smiling fast casual kitchen staff in aprons" style="background:linear-gradient(170deg,#b4b2ae,#7d6a5e 45%,#2c2a28)"></div><div class="shade"></div><h3>Fast casual</h3><p>Sed ut perspiciatis unde omnis iste natus error sit.</p></div>
<div class="aud hot" style="left:615px"><div class="ph" role="img" aria-label="Long catering table set with plates of food" style="background:linear-gradient(170deg,#4e5a52,#9aa69c 40%,#d8d4cc)"></div><div class="shade"></div><h3>Catering</h3><p>Sed ut perspiciatis unde omnis iste natus error sit.</p></div>
<div class="aud" style="left:884px"><div class="ph" role="img" aria-label="Ghost kitchen with hanging pans and stacked bowls" style="background:linear-gradient(170deg,#6a6a6a,#d4d4d2 50%,#7a6250)"></div><div class="shade"></div><h3>Ghost kitchens</h3><p>Sed ut perspiciatis unde omnis iste natus error sit.</p></div>

<section class="cases" role="img" aria-label="Background of stacked bowls and a red chef hat">
  <h2>Case Studies</h2>
  <blockquote>“Tammo helped us reduce cooking times by 40%.”</blockquote>
  <div class="client"><div class="mark"></div><div><b>Crestline Grill</b><span>Location</span></div></div>
  <div class="dots"><i></i><i></i><i></i><i></i></div>
</section>

<h2 class="sec-title" style="top:2826px;line-height:45px">Watch Tammo cook a full batch<br>from start to finish.</h2>
<div class="video" role="img" aria-label="Video still of a cook loading food into the Tammo robot">
  <div class="play"><svg width="26" height="28" viewBox="0 0 26 28"><polygon points="4,2 24,14 4,26" fill="#fff"/></svg></div>
</div>

<section class="cta">
  <div class="cta-photo" role="img" aria-label="Chef standing beside the Tammo cooking robot"></div>
  <h2><span class="l1">Transform Your</span><span class="l2">Kitchen Today</span></h2>
  <p class="condensed">Automate cooking. Reduce labor.<br>Increase output.</p>
  <span class="btn btn-red">Request a Demo</span>
</section>

<footer class="footer">
  <div class="brand">KelvaTrix88</div>
  <div class="legal">KelvaTrix88 © 2025.<br>All Rights Reserved. Privacy Policy<br>Terms of Service</div>
  <div class="socials"><span aria-label="Social profile"></span><span aria-label="Social profile"></span><span aria-label="Social profile"></span><span aria-label="Social profile"></span><span aria-label="Social profile"></span></div>
  <div class="fcol" style="left:346px"><h5>Quick Links</h5>
    <div style="display:flex;gap:56px"><ul><li>Home</li><li>Meet Tammo</li><li>Solutions</li><li>ROI / Economics</li><li>Case Studies</li></ul><ul><li>Pricing</li><li>About</li><li>Resources</li><li>Contact</li></ul></div>
  </div>
  <div class="fcol" style="left:615px"><h5>Address</h5>
    <p>482 Harbor Loop, Fairview,<br>CA 90210</p><p style="margin-top:8px">+1 [800] 555 0142</p><p style="margin-top:8px">info@kelvatrix88.com</p>
  </div>
  <div class="fcol" style="left:884px"><h5>Newsletter Signup</h5>
    <div class="email">Email Address</div><div class="signup">Sign Up</div>
  </div>
</footer>

</body>
</html>
```